Sleek wordpress site for Bramblecrest finishing works

We are a commercial job shop that serves B2B, govt & LEO and retail clients.We need a wordpress site with 6 individual pages: homepage, coating, laser engraving, laser cutting, part marking, and contact us. I have attached an outline of the desired flow and sub headings for each page. I would like to incorporate the colors of the logo through out the site to be clean and sleek enough to appeal to B2B commercial clients yet be inviting enough for retail clients.

I would like to have easy picture functionality so photographs on each page can be updated easily.

Target Market(s)

B2B industrial & Govt and Military part marking, laser engraving and coating: machine shops, aerospace companies, tool manufactures. Retail: personalized gifts, Job Shop

Coding

Coded - Design and coding required

Font styles to use
Sans Serif
Other font styles liked:
• Open to suggestion

Colors
0255a3
3176b5
eaf1f7
cfdeed
ffffff

Requirements
Must have
• Clean easy to navigate flow, separate pages as indicated on attached outline, high class feel. Great picture functionality, professional and inviting feel,
• **update: needs to be optimized for mobile, should have a gallery function. Gallery can be an additional page or embedded
Nice to have
• Social media connectivity links,
Should not have
• crappy plugins that make back-end management difficult, no blog

```html
<!DOCTYPE html>
<html lang="en">
<head>
<meta charset="utf-8">
<title>Bramblecrest Finishing Works</title>
<link rel="stylesheet" href="https://fonts.googleapis.com/css2?family=Lato:wght@400;700;900&family=Open+Sans:ital,wght@0,400;0,600;0,700;1,400&display=swap">
<style>
:root{
  --blue:#0255a3;
  --blue-mid:#3176b5;
  --blue-pale:#eaf1f7;
  --blue-soft:#cfdeed;
  --navy:#0b2f6b;
  --white:#ffffff;
  --ink:#1c1c1c;
  --grey:#666;
  --ghost:#e9edf2;
  --footer:#101112;
}
*{box-sizing:border-box;margin:0;padding:0}
html,body{width:1200px;height:3797px;overflow:hidden}
body{position:relative;background:var(--white);font-family:"Open Sans",Arial,sans-serif;color:var(--ink)}
.abs{position:absolute}
h1,h2,h3,.nav,.btn{font-family:"Lato",Arial,sans-serif}

/* header */
.brand{left:96px;top:22px;display:flex;align-items:center;gap:14px}
.brand-mark{width:40px;height:40px;background:var(--blue)}
.brand-name{font-family:"Lato",sans-serif;font-weight:900;font-size:19px;line-height:1.15;color:var(--blue);text-transform:uppercase;width:200px}
.contact-top{left:520px;top:32px;display:flex;gap:22px;align-items:flex-start}
.contact-top .phone{font-size:20px;font-weight:600;color:#222;line-height:24px}
.contact-top .mail{font-size:15px;color:#333}
.search{left:848px;top:40px;width:255px;height:34px;border:1px solid #ccc;border-radius:17px;font-size:12px;color:#999;padding:8px 18px}
.search svg{position:absolute;right:14px;top:8px}
.nav{left:340px;top:114px;width:860px;height:53px;background:var(--blue);clip-path:polygon(30px 0,100% 0,100% 100%,0 100%);display:flex;align-items:center;padding-left:34px}
.nav a{color:var(--white);text-decoration:none;font-size:14px;padding:0 19px;height:53px;line-height:53px;letter-spacing:.3px;white-space:nowrap;flex:none}
.nav a.active{background:var(--navy)}

/* hero */
.hero{left:0;top:167px;width:1200px;height:668px;background:radial-gradient(circle at 38% 70%,#f3a34a 0,#a35a1e 12%,#3a2a22 32%,#15171a 65%)}
.hero h1{left:730px;top:230px;color:var(--white);font-size:48px;font-weight:900;white-space:nowrap}
.hero p{left:730px;top:300px;width:380px;color:var(--white);font-size:15px;line-height:25px;font-weight:600}
.hero .btn{left:730px;top:408px;width:198px;height:44px;border:2px solid var(--white);border-radius:22px;color:var(--white);font-size:14px;font-weight:700;text-align:center;line-height:40px}
.dots{left:562px;top:580px;display:flex;gap:8px}
.dots i{width:18px;height:18px;border-radius:50%;border:2px solid var(--white);display:block}
.dots i.on{background:var(--white)}
.hero-curve{left:0;top:660px}

/* section titles */
.ghost{font-family:"Lato",sans-serif;font-weight:900;color:var(--ghost);text-transform:uppercase;white-space:nowrap}
.title{font-family:"Lato",sans-serif;font-weight:900;text-transform:uppercase;color:#111;white-space:nowrap}

/* services */
.services-ghost{left:0;width:1200px;top:915px;text-align:center;font-size:72px}
.services-title{left:0;width:1200px;top:935px;text-align:center;font-size:34px}
.services-sub{left:0;width:1200px;top:998px;text-align:center;font-size:13px;color:#555}
.service{top:1060px;width:230px;text-align:center}
.service .pin{margin:0 auto 14px;width:110px;height:124px}
.service h3{font-size:16px;font-weight:700;margin-bottom:8px;text-transform:uppercase}
.service p{font-size:12px;line-height:20px;color:var(--grey)}

.tiles{left:0;top:1385px;width:1200px;height:278px;display:flex}
.tile{flex:1;position:relative;display:flex;align-items:center;justify-content:center}
.tile span{font-family:"Lato",sans-serif;font-size:24px;font-weight:700;color:rgba(255,255,255,.35);text-transform:uppercase;position:absolute;bottom:50px;white-space:nowrap}
.tile.active span{color:var(--white);bottom:auto;top:120px}

/* about */
.about-ghost{left:752px;top:1700px;font-size:72px}
.about-title{left:96px;top:1766px;font-size:34px}
.about-text{left:96px;top:1838px;width:545px;font-size:13px;line-height:22px;color:var(--grey)}
.about-text p{margin-bottom:12px}
.read-more{left:96px;top:2040px;width:162px;height:40px;border-radius:20px;background:var(--navy);color:var(--white);font-size:14px;font-weight:700;text-align:center;line-height:40px}
.video-frame{left:726px;top:1783px;width:408px;height:285px;border-top:3px solid var(--blue);border-right:3px solid var(--blue)}
.video{left:699px;top:1813px;width:400px;height:268px;background:linear-gradient(135deg,#8f9aa6,#d9dde2 40%,#a2aab3 70%,#5e6874);box-shadow:0 2px 8px rgba(0,0,0,.3)}
.video svg{position:absolute;left:176px;top:110px}

.divider{left:96px;top:2178px;width:1005px;height:1px;background:#ddd}

/* clients & testimonials */
.clients-ghost{left:0;top:2242px;font-size:46px}
.clients-title{left:96px;top:2258px;font-size:23px}
.arrows{font-size:20px;color:#888;letter-spacing:14px}
.client-grid{left:96px;top:2317px;width:486px;display:grid;grid-template-columns:repeat(3,148px);gap:29px 21px}
.client{height:74px;border:1px solid #ddd;box-shadow:0 1px 4px rgba(0,0,0,.12);display:flex;align-items:center;justify-content:center;gap:8px;font-family:"Lato",sans-serif;font-weight:700;font-size:17px;color:#333}
.client i{width:10px;height:10px;background:#333;display:block}
.testi-ghost{left:830px;top:2242px;font-size:46px}
.testi-title{left:628px;top:2258px;font-size:23px}
.quote{left:628px;top:2309px;width:473px;height:142px;background:#ddd;border:1px solid #ccc;padding:22px 28px 0 46px;font-size:12px;line-height:21px;font-style:italic;color:#555}
.quote b{position:absolute;left:20px;top:10px;font-size:36px;color:#999;font-style:normal}
.quote-tip{left:684px;top:2451px;width:0;height:0;border-left:14px solid transparent;border-right:14px solid transparent;border-top:14px solid #ddd}
.author{left:705px;top:2476px;font-size:16px;font-weight:600}
.author em{font-size:11px;color:#666;font-weight:400}

/* gallery */
.gallery-bg{left:0;top:2583px;width:1200px;height:785px;background:linear-gradient(#eef1f5,#f6f8fa 60%,#fff)}
.gallery-ghost{left:0;width:1200px;top:2650px;text-align:center;font-size:60px;color:#dde2e8}
.gallery-title{left:0;width:1200px;top:2664px;text-align:center;font-size:34px}
.gallery-sub{left:300px;width:600px;top:2727px;text-align:center;font-size:13px;line-height:22px;color:#555}
.gallery{left:96px;top:2805px;width:1005px;display:grid;grid-template-columns:repeat(4,1fr);gap:10px 10px}
.gallery div{height:188px;position:relative}
.zoom{position:absolute;left:50%;top:50%;width:42px;height:42px;margin:-21px;border-radius:50%;background:var(--blue-mid);color:#fff;font-size:30px;line-height:40px;text-align:center}

/* footer */
.footer-curve{left:0;top:3280px}
.footer{left:0;top:3385px;width:1200px;height:412px;background:var(--footer);color:#ddd}
.f-head{font-family:"Lato",sans-serif;font-weight:700;font-size:18px;color:#fff;text-transform:uppercase;position:absolute;top:20px}
.f-head span{color:var(--blue-mid)}
.links{left:96px;top:78px;list-style:none;font-size:13px;line-height:25.5px}
.links li::before{content:"»";margin-right:10px;color:#aaa}
.f-contact{left:325px;top:78px;font-size:13px;line-height:21px}
.f-contact .row{display:flex;gap:18px;margin-bottom:14px}
.f-quote-text{left:632px;top:75px;width:470px;font-size:13px;line-height:22px}
.field{height:42px;border:1px solid #888;font-size:12px;padding:12px 12px;color:#ccc}
.submit{background:var(--blue);color:#fff;font-family:"Lato",sans-serif;font-weight:900;font-size:17px;text-align:center;line-height:40px;padding:0}
.f-line{left:96px;top:332px;width:1005px;height:1px;background:#333}
.copy{left:96px;top:355px;font-size:13px}
.follow{left:832px;top:350px;display:flex;align-items:center;gap:8px;font-family:"Lato",sans-serif;font-weight:700;font-size:18px;color:#fff}
.follow span{color:var(--blue-mid);margin-right:8px;margin-left:-4px}
.follow i{width:28px;height:28px;border:2px solid #ddd;border-radius:50%;display:block}
</style>
</head>
<body>

<header>
  <div class="abs brand">
    <div class="brand-mark"></div>
    <div class="brand-name">Bramblecrest Finishing Works</div>
  </div>
  <div class="abs contact-top">
    <svg width="26" height="30" viewBox="0 0 24 24"><path fill="#0255a3" d="M6.6 10.8c1.4 2.8 3.8 5.1 6.6 6.6l2.2-2.2c.3-.3.7-.4 1-.2 1.1.4 2.3.6 3.6.6.6 0 1 .4 1 1V20c0 .6-.4 1-1 1C10.6 21 3 13.4 3 4c0-.6.4-1 1-1h3.5c.6 0 1 .4 1 1 0 1.3.2 2.5.6 3.6.1.3 0 .7-.2 1z"/></svg>
    <div>
      <div class="phone">555.214.0386</div>
      <div class="mail">hello@bramblecrestworks.com</div>
    </div>
  </div>
  <div class="abs search">Search here
    <svg width="16" height="16" viewBox="0 0 16 16"><circle cx="6.5" cy="6.5" r="5" fill="none" stroke="#888" stroke-width="1.6"/><path d="M10.5 10.5L15 15" stroke="#888" stroke-width="1.6"/></svg>
  </div>
  <nav class="abs nav">
    <a class="active">HOME</a><a>COATING</a><a>LASER ENGRAVING</a><a>LASER CUTTING</a><a>PART MARKING</a><a>CONTACT</a>
  </nav>
</header>

<section class="abs hero" role="img" aria-label="Laser cutting head throwing sparks onto a metal sheet">
  <h1 class="abs">LASER CUTTING</h1>
  <p class="abs">Sed ut perspiciatis unde omnis iste at natus error sit voluptatem accusantium doloremque laudantium, tot am rem aperiam, saque ipsa quae</p>
  <div class="abs btn">GET MORE INFO ➔</div>
  <div class="abs dots"><i class="on"></i><i></i><i></i></div>
  <svg class="abs hero-curve" width="1200" height="180" viewBox="0 0 1200 180">
    <path d="M0 20 Q600 170 1200 40 L1200 180 L0 180Z" fill="#0b2f6b"/>
    <path d="M0 30 Q600 170 1200 52 L1200 180 L0 180Z" fill="#fff"/>
    <path d="M140 108 Q600 200 1130 80" fill="none" stroke="#0255a3" stroke-width="6"/>
    <path d="M0 40 Q600 185 1200 62 L1200 180 L0 180Z" fill="#fff"/>
  </svg>
</section>

<section>
  <div class="abs ghost services-ghost">OUR SERVICES</div>
  <h2 class="abs title services-title">OUR SERVICES</h2>
  <p class="abs services-sub">We offer the wide range of services to help our customer's create whatever they needs</p>

  <div class="abs service" style="left:99px">
    <svg class="pin" viewBox="0 0 110 124"><path d="M55 4a51 51 0 0 1 20 98L55 122 35 102A51 51 0 0 1 55 4z" fill="#0255a3"/><circle cx="55" cy="55" r="38" fill="none" stroke="#fff" stroke-width="3"/><rect x="40" y="40" width="30" height="30" fill="none" stroke="#fff" stroke-width="3"/><path d="M46 64L64 46" stroke="#fff" stroke-width="3"/></svg>
    <h3>Laser Engraving</h3>
    <p>Capabilities include CO2 and fiber lasers, so a wide selection of materials and substrates can be</p>
  </div>
  <div class="abs service" style="left:353px">
    <svg class="pin" viewBox="0 0 110 124"><path d="M55 4a51 51 0 0 1 20 98L55 122 35 102A51 51 0 0 1 55 4z" fill="#0255a3"/><circle cx="55" cy="55" r="38" fill="none" stroke="#fff" stroke-width="3"/><path d="M40 40L70 70M70 40L40 70" stroke="#fff" stroke-width="3"/><circle cx="40" cy="70" r="5" fill="none" stroke="#fff" stroke-width="3"/><circle cx="70" cy="70" r="5" fill="none" stroke="#fff" stroke-width="3"/></svg>
    <h3>Laser Cutting</h3>
    <p>We can custom cut virtually any shape or design in a variety of substrates or materials. Custom cut items can be</p>
  </div>
  <div class="abs service" style="left:615px">
    <svg class="pin" viewBox="0 0 110 124"><path d="M55 4a51 51 0 0 1 20 98L55 122 35 102A51 51 0 0 1 55 4z" fill="#0255a3"/><circle cx="55" cy="55" r="38" fill="none" stroke="#fff" stroke-width="3"/><path d="M45 36h20v10l-10 30-10-30z" fill="none" stroke="#fff" stroke-width="3"/><path d="M36 74h38" stroke="#fff" stroke-width="3"/></svg>
    <h3>Part Marking</h3>
    <p>Serial numbers, barcodes and data plates marked to spec, with clean lasting results on most metal parts</p>
  </div>
  <div class="abs service" style="left:873px">
    <svg class="pin" viewBox="0 0 110 124"><path d="M55 4a51 51 0 0 1 20 98L55 122 35 102A51 51 0 0 1 55 4z" fill="#0255a3"/><circle cx="55" cy="55" r="38" fill="none" stroke="#fff" stroke-width="3"/><rect x="38" y="42" width="22" height="14" rx="3" fill="none" stroke="#fff" stroke-width="3"/><path d="M46 56v16M62 46l12-6M62 50h12M62 54l12 6" stroke="#fff" stroke-width="3"/></svg>
    <h3>Coating</h3>
    <p>A durable ceramic based finish that can be applied to metals, plastics, polymers and wood. The</p>
  </div>
</section>

<section class="abs tiles">
  <div class="tile" role="img" aria-label="Laser engraving machine at work" style="background:linear-gradient(160deg,#2a2f36,#5d4a3a 60%,#c9772e)"><span>Laser Engraving</span></div>
  <div class="tile active" role="img" aria-label="Laser cutting head with sparks" style="background:linear-gradient(180deg,#3c4046,#22252a 60%,#6a4a2a)"><span>Laser Cutting</span></div>
  <div class="tile" role="img" aria-label="Part marking with bright sparks" style="background:radial-gradient(circle at 50% 70%,#b77bd0,#5a3a4a 30%,#1e1c22 70%)"><span>Part Marking</span></div>
  <div class="tile" role="img" aria-label="Spray coating applied to a metal part" style="background:linear-gradient(160deg,#1b2026,#3d4450 50%,#8a4a30)"><span>Coatings</span></div>
</section>

<section>
  <div class="abs ghost about-ghost">ABOUT US</div>
  <h2 class="abs title about-title">About Bramblecrest Finishing</h2>
  <div class="abs about-text">
    <p>Nemo enim ipsam voluptatem quia voluptas sit aspernatur aut odit aut fugit, sed quia consequuntur magni dolores eos qui ratione voluptatem sequi nesciunt.</p>
    <p>Neque porro quisquam est, qui dolorem ipsum quia dolor sit amet, consectetur, adipisci velit, sed quia non numquam eius modi tempora incidunt ut labore et dolore magnam aliquam quaerat voluptatem. Ut enim ad minima veniam, quis nostrum exercitationem ullam corporis suscipit laboriosam, nisi ut aliquid commodi consequatur...</p>
  </div>
  <div class="abs read-more btn">READ MORE ➔</div>
  <div class="abs video-frame"></div>
  <div class="abs video" role="img" aria-label="Video still of a laser etching lettering into metal">
    <svg width="48" height="48" viewBox="0 0 48 48"><circle cx="24" cy="24" r="24" fill="#fff"/><path d="M19 14l14 10-14 10z" fill="#0255a3"/></svg>
  </div>
</section>

<div class="abs divider"></div>

<section>
  <div class="abs ghost clients-ghost">OUR CLIENTS</div>
  <h2 class="abs title clients-title">Our Clients</h2>
  <div class="abs arrows" style="left:548px;top:2258px">‹›</div>
  <div class="abs client-grid">
    <div class="client"><i></i>Northwind</div>
    <div class="client">Veltrix</div>
    <div class="client">Cobalta</div>
    <div class="client">Harrowgate</div>
    <div class="client">Orbisol</div>
    <div class="client"><i></i>Kestrel</div>
  </div>
  <div class="abs ghost testi-ghost">TESTIMONIALS</div>
  <h2 class="abs title testi-title">Testimonials</h2>
  <div class="abs arrows" style="left:1068px;top:2258px">‹›</div>
  <div class="abs quote"><b>“</b>At vero eos et accusamus et iusto odio dignissimos ducimus qui blanditiis per sentium voluptatum deleniti atque corrupti quos dolores et quas molestias excepturi sint occaecati cupiditate non provident</div>
  <div class="abs quote-tip"></div>
  <div class="abs author">Mara Ellison, <em>Creative Manager, USA</em></div>
</section>

<section>
  <div class="abs gallery-bg"></div>
  <div class="abs ghost gallery-ghost">RECENT WORK</div>
  <h2 class="abs title gallery-title">Our Gallery</h2>
  <p class="abs gallery-sub">At vero eos et accusamus et iusto odio dignissimos ducimus qui blanditiis praesentium voluptatum deleniti atque corrupti quos dolores et quas molestias excepturi sint occaecati cupiditate non provident</p>
  <div class="abs gallery">
    <div role="img" aria-label="Laser head over metal sheet" style="background:linear-gradient(150deg,#c6cbd2,#7e4a4a 55%,#2a1c1e)"></div>
    <div role="img" aria-label="Sparks from laser cutting" style="background:radial-gradient(circle at 50% 40%,#f6c27a,#9a5a24 35%,#2a2420 75%)"><span class="zoom">+</span></div>
    <div role="img" aria-label="Laser cutting head in dark workshop" style="background:linear-gradient(160deg,#1c1f24,#3a3e44 60%,#6a5a44)"></div>
    <div role="img" aria-label="Cut metal parts with sparks" style="background:linear-gradient(150deg,#e2a45a,#8a7460 50%,#c7c2b8)"></div>
    <div role="img" aria-label="Sparks spraying under laser" style="background:radial-gradient(circle at 40% 40%,#f7b55a,#8a4a1e 35%,#1e1a18 75%)"></div>
    <div role="img" aria-label="Laser cutting sheet metal" style="background:linear-gradient(160deg,#2a2e34,#6a6e76 55%,#c9ccd0)"></div>
    <div role="img" aria-label="Laser cut patterned plate" style="background:linear-gradient(150deg,#6a5a4a,#c99a5a 45%,#3a3430)"></div>
    <div role="img" aria-label="Blue lit laser marking metal" style="background:linear-gradient(160deg,#1a2a4a,#3a5a8a 50%,#0e1420)"></div>
  </div>
</section>

<svg class="abs footer-curve" width="1200" height="110" viewBox="0 0 1200 110">
  <path d="M0 100 Q600 -20 1200 90 L1200 110 L0 110Z" fill="#0b2f6b"/>
  <path d="M60 82 Q600 -10 1140 70" fill="none" stroke="#0255a3" stroke-width="6"/>
  <path d="M0 106 Q600 5 1200 100 L1200 110 L0 110Z" fill="#101112"/>
</svg>

<footer class="abs footer">
  <div class="f-head" style="left:96px">Quick <span>Links</span></div>
  <ul class="abs links">
    <li>Home</li><li>Coating</li><li>Laser Engraving</li><li>Laser Cutting</li><li>Part Marking</li><li>Gallery</li><li>Contact Us</li>
  </ul>
  <div class="f-head" style="left:325px">Contact <span>Us</span></div>
  <div class="abs f-contact">
    <div class="row"><svg width="14" height="20" viewBox="0 0 14 20"><path d="M7 0a7 7 0 0 1 7 7c0 5-7 13-7 13S0 12 0 7a7 7 0 0 1 7-7z" fill="#fff"/><circle cx="7" cy="7" r="2.5" fill="#101112"/></svg><div>118 Ridgefield Ave #4, Dunmore,<br>AZ 85900</div></div>
    <div class="row"><svg width="14" height="16" viewBox="0 0 24 24"><path fill="#fff" d="M6.6 10.8c1.4 2.8 3.8 5.1 6.6 6.6l2.2-2.2c.3-.3.7-.4 1-.2 1.1.4 2.3.6 3.6.6.6 0 1 .4 1 1V20c0 .6-.4 1-1 1C10.6 21 3 13.4 3 4c0-.6.4-1 1-1h3.5c.6 0 1 .4 1 1 0 1.3.2 2.5.6 3.6.1.3 0 .7-.2 1z"/></svg><div>(+1) 555 302 1147</div></div>
    <div class="row"><svg width="14" height="14" viewBox="0 0 14 14"><circle cx="7" cy="7" r="6" fill="none" stroke="#fff" stroke-width="1.5"/><path d="M7 3v4h3" stroke="#fff" stroke-width="1.5" fill="none"/></svg><div>Mon - Weds:&nbsp;&nbsp;&nbsp;9am-5:30pm<br>Thu - Fri:&nbsp;&nbsp;&nbsp;&nbsp;&nbsp;&nbsp;9am-7pm<br>Sat - Sun:&nbsp;&nbsp;&nbsp;&nbsp;&nbsp;11am-3pm</div></div>
  </div>
  <div class="f-head" style="left:632px">Get a <span>Quote</span></div>
  <p class="abs f-quote-text">Bramblecrest Finishing offer the wide range of services to help our customer's create whatever they needs.</p>
  <div class="abs field" style="left:632px;top:143px;width:226px">Name</div>
  <div class="abs field" style="left:875px;top:143px;width:226px">Email</div>
  <div class="abs field" style="left:632px;top:199px;width:226px">Phone No</div>
  <div class="abs field submit" style="left:875px;top:199px;width:226px;border-color:var(--blue)">SUBMIT</div>
  <div class="abs f-line"></div>
  <div class="abs copy">Copyrights © 2018 Bramblecrest Finishing.&nbsp; All Rights Reserved &nbsp;&nbsp;|&nbsp;&nbsp; Privacy Policy.</div>
  <div class="abs follow">FOLLOW <span>US</span><i aria-label="Social profile one"></i><i aria-label="Social profile two"></i><i aria-label="Social profile three"></i><i aria-label="Social profile four"></i></div>
</footer>

</body>
</html>
```